Harbor Loom Floors Letterhead

Letterhead used for business reasons. It must be editable and easy to use.

Address is 2715 W. Pelican Lane Seabright NC 34187 - 910.382.6519

```html
<!DOCTYPE html>
<html lang="en">
<head>
<meta charset="utf-8">
<title>Harbor Loom Floors Letterhead</title>
<link href="https://fonts.googleapis.com/css2?family=Source+Sans+3:wght@400&family=Montserrat:wght@400&display=swap" rel="stylesheet">
<style>
  :root {
    --backdrop: #e8e5e1;
    --paper: #ffffff;
    --brand-orange: #d9861f;
    --salutation-navy: #1c2a4a;
    --body-grey: #3d3d3d;
    --contact-ink: #222222;
    --signature-tone: #d6d6d6;
  }
  * { margin: 0; padding: 0; box-sizing: border-box; }
  html, body {
    width: 1200px;
    height: 1141px;
    overflow: hidden;
    background: var(--backdrop);
  }
  .letterhead {
    position: absolute;
    left: 211px;
    top: 20px;
    width: 779px;
    height: 1101px;
    background: var(--paper);
    box-shadow: 0 6px 18px rgba(0,0,0,0.18);
    font-family: "Source Sans 3", sans-serif;
  }
  .brand-name {
    position: absolute;
    left: 77px;
    top: 64px;
    font-weight: 400;
    font-size: 40px;
    line-height: 46px;
    color: var(--brand-orange);
  }
  .salutation {
    position: absolute;
    left: 77px;
    top: 284px;
    font-size: 18.5px;
    line-height: 22px;
    color: var(--salutation-navy);
  }
  .letter-body {
    position: absolute;
    left: 77px;
    top: 368px;
    width: 625px;
  }
  .letter-body p {
    font-size: 13.5px;
    line-height: 15.7px;
    color: var(--body-grey);
    text-align: justify;
    height: 110px;
  }
  .closing {
    position: absolute;
    left: 77px;
    top: 918px;
    font-size: 13.5px;
    line-height: 16px;
    color: var(--body-grey);
  }
  .signature-area {
    position: absolute;
    left: 77px;
    top: 990px;
    width: 210px;
    height: 52px;
    background: linear-gradient(90deg, var(--signature-tone), #efefef);
    border-radius: 3px;
  }
  .contact-block {
    position: absolute;
    right: 76px;
    top: 970px;
    text-align: right;
    font-family: "Montserrat", sans-serif;
    font-style: normal;
    font-size: 13.4px;
    line-height: 18px;
    color: var(--contact-ink);
  }
  .contact-phone {
    margin-top: 10px;
    display: flex;
    align-items: center;
    justify-content: flex-end;
    gap: 6px;
  }
  .contact-phone svg { width: 11px; height: 11px; }
</style>
</head>
<body>
  <main class="letterhead">
    <header class="brand-name">Harbor Loom<br>Floors</header>

    <p class="salutation">Dear Mr. Carver</p>

    <section class="letter-body">
      <p>Lorem Ipsum is simply dummy text of the printing and typesetting industry. Lorem Ipsum has been the industry's standard dummy text ever since the 1500s, when an unknown printer took a galley of type and scrambled it to make a type specimen book. It has survived not only five centuries, but also the leap into electronic typesetting, remaining essentially unchanged. It was popularised in the 1960s with the release of Letraset sheets containing Lorem Ipsum passages</p>
      <p>Lorem Ipsum is simply dummy text of the printing and typesetting industry. Lorem Ipsum has been the industry's standard dummy text ever since the 1500s, when an unknown printer took a galley of type and scrambled it to make a type specimen book. It has survived not only five centuries, but also the leap into electronic typesetting, remaining essentially unchanged. It was popularised in the 1960s with the release of Letraset sheets containing Lorem Ipsum passages</p>
      <p>Lorem Ipsum is simply dummy text of the printing and typesetting industry. Lorem Ipsum has been the industry's standard dummy text ever since the 1500s, when an unknown printer took a galley of type and scrambled it to make a type specimen book. It has survived not only five centuries, but also the leap into electronic typesetting, remaining essentially unchanged. It was popularised in the 1960s with the release of Letraset sheets containing Lorem Ipsum passages</p>
      <p>Lorem Ipsum is simply dummy text of the printing and typesetting industry. Lorem Ipsum has been the industry's standard dummy text ever since the 1500s, when an unknown printer took a galley of type and scrambled it to make a type specimen book. It has survived not only five centuries, but also the leap into electronic typesetting, remaining essentially unchanged. It was popularised in the 1960s with the release of Letraset sheets containing Lorem Ipsum passages</p>
      <p>Lorem Ipsum is simply dummy text of the printing and typesetting industry. Lorem Ipsum has been the industry's standard dummy text ever since the 1500s, when an unknown printer took a galley of type and scrambled it to make a type specimen book. It has survived not only five centuries, but also the leap into electronic typesetting, remaining essentially unchanged. It was popularised in the 1960s with the release of Letraset sheets containing Lorem Ipsum passages</p>
    </section>

    <p class="closing">Sincerely</p>

    <div class="signature-area" role="img" aria-label="Handwritten signature of the sender"></div>

    <address class="contact-block">
      <div>2715 W. Pelican Lane</div>
      <div>Seabright NC 34187</div>
      <div class="contact-phone">
        <span>910.382.6519</span>
        <svg viewBox="0 0 24 24" aria-hidden="true">
          <path fill="var(--brand-orange)" d="M6.6 10.8a15.1 15.1 0 0 0 6.6 6.6l2.2-2.2a1 1 0 0 1 1-.25 11.4 11.4 0 0 0 3.6.57 1 1 0 0 1 1 1V20a1 1 0 0 1-1 1A17 17 0 0 1 3 4a1 1 0 0 1 1-1h3.5a1 1 0 0 1 1 1c0 1.25.2 2.45.57 3.57a1 1 0 0 1-.25 1z"/>
        </svg>
      </div>
    </address>
  </main>
</body>
</html>
```